Calder Vane LED - E- Commerce site

We need a website designed for an LED Billboard company that sells:
1) LED Billboards (Sales & Rental)
2) LED Gas Station lights
3) Truss Systems (Sales & Rental)
4) Sound Systems (Sales & Rental)

Attached are websites that sell similar products as Calder Vane LED. Target market is for business, property managers and event coordinators.
This site will need to be an e-commerce site where customers can purchase the product directly from the site. What I'm looking for is a design layout to start.

Conceptual Web Designs:
http://192.0.2.47:8087/index.html
http://www.pmvdisplay.example/
http://www.auralomaaudio.example/
http://www.quillmarkpanel.example/

Attached is the logo of the company: Please note that the new spelling of the logo is "Calder Vane LED" using domain " CalderVaneLED.com

Industry/Entity Type

Gas Station

Number of Pages Required

5+ page

Requirements
Must have
• 1) E-Commerce - Customers will need to be able to order product from the site.
• 2) Customers will also have the option to rent the product as well.
Nice to have
• I like the image of the attached website, that has a video clip loop
• http://www.quillmarkpanel.example/

```html
<!DOCTYPE html>
<html lang="en">
<head>
<meta charset="utf-8">
<title>Calder Vane LED</title>
<link href="https://fonts.googleapis.com/css2?family=Ubuntu:wght@400;500;700&family=Oswald:wght@400;500&display=swap" rel="stylesheet">
<style>
:root{
  --ink:#1c1c1c;
  --header:#1b1b1b;
  --red:#e3262f;
  --yellow:#fcc40a;
  --grey-band:#e6e6e6;
  --line:#dcdcdc;
  --text:#333;
  --muted:#777;
  --price:#e3262f;
  --link:#2a6fc9;
  --footer:#161616;
  --footer-text:#9a9a9a;
}
*{box-sizing:border-box;margin:0;padding:0}
html,body{width:1200px;height:2308px;overflow:hidden}
body{font-family:"Ubuntu",sans-serif;color:var(--text);background:#fff;font-size:13px}
.wrap{width:938px;margin:0 auto;position:relative}
a{color:inherit;text-decoration:none}

/* header */
.site-header{background:var(--header);height:135px}
.site-header .wrap{height:135px}
.top-links{position:absolute;right:0;top:14px;display:flex;gap:22px;font-size:11px;color:#b5b5b5;letter-spacing:.3px}
.top-links .phone{color:var(--red)}
.brand{position:absolute;left:0;top:40px;display:flex;align-items:center;gap:12px}
.brand-dot{width:46px;height:46px;border-radius:50%;background:var(--yellow)}
.brand-name{font-size:26px;font-weight:700;color:var(--yellow)}
.search{position:absolute;left:410px;top:61px;width:331px;height:41px;border:1px solid #3a3a3a;display:flex;align-items:center}
.search span{flex:1;padding-left:16px;font-size:11px;font-style:italic;color:#666}
.search .btn{width:44px;height:100%;border-left:1px solid #3a3a3a;display:flex;align-items:center;justify-content:center}
.cart{position:absolute;right:0;top:61px;width:168px;height:41px;border:1px solid #3a3a3a;display:flex;align-items:center;gap:10px;padding-left:16px;color:#eee;font-size:12px}

/* nav */
.main-nav{background:var(--red);height:46px}
.main-nav ul{list-style:none;display:flex;height:46px}
.main-nav li{padding:0 20px;line-height:46px;color:#fff;font-size:12.5px;text-transform:uppercase}
.main-nav li.active{background:var(--yellow);color:var(--ink);padding:0 20px}

/* hero */
.hero{height:397px;background:linear-gradient(180deg,#bfe2f3,#8ccbe8 50%,#a9d8ee);padding-top:31px}
.hero .wrap{height:335px}
.slide{position:absolute;left:0;top:0;width:634px;height:334px;background:linear-gradient(180deg,#f4f6f8,#e4e9ee 60%,#f6f7f8)}
.slide-title{position:absolute;left:20px;top:216px;font-family:"Oswald",sans-serif;font-size:30px;line-height:36px;color:#222;text-transform:uppercase;letter-spacing:-.3px}
.slide-title em{font-style:normal;color:var(--red)}
.btn-yellow{display:inline-block;background:var(--yellow);color:var(--ink);font-weight:700;font-size:11px;text-transform:uppercase}
.slide .btn-yellow{position:absolute;left:21px;top:285px;padding:9px 17px}
.slide-arrows{position:absolute;right:23px;top:285px;display:flex;gap:4px}
.slide-arrows span{width:29px;height:29px;background:var(--yellow);display:flex;align-items:center;justify-content:center}
.promo{position:absolute;left:650px;width:288px;height:158px;padding:12px 18px;color:#fff}
.promo.sound{top:0;background:linear-gradient(90deg,#111 40%,#3a3a3a)}
.promo.truss{top:176px;background:linear-gradient(90deg,#c631b7,#7d2b9a)}
.promo h3{font-family:"Oswald",sans-serif;font-size:34px;line-height:34px;font-weight:500;text-transform:uppercase}
.promo.sound h3{color:#e8277d}
.promo.truss h3{color:#f8e36c}
.promo h4{font-size:15px;font-weight:700;text-transform:uppercase;margin-top:2px}
.promo p{font-size:12px;text-transform:uppercase;margin-top:4px}
.promo .btn-yellow{position:absolute;padding:8px 16px}
.promo .off{position:absolute;font-size:26px;font-family:"Oswald",sans-serif}
.promo .off small{font-size:14px;vertical-align:super}
.promo.sound .btn-yellow{left:18px;top:114px}
.promo.sound .off{right:20px;top:108px;color:#fff}
.promo.sound .off b{color:#41c7e8;font-weight:400}
.promo.truss .btn-yellow{right:18px;top:114px}
.promo.truss .off{left:18px;top:108px}
.promo.truss .off b{color:#41c7e8;font-weight:400}

/* featured */
.featured{padding-top:40px;height:1491px;height:auto}
.section-head{display:flex;justify-content:space-between;align-items:center;height:34px}
.section-head h2{font-size:19px;font-weight:500;text-transform:uppercase;color:#222}
.filters{display:flex;gap:4px;font-size:11px;text-transform:uppercase;color:#555}
.filters span{padding:8px 12px}
.filters .on{background:#e2e2e2;color:#111}
.grid{display:grid;grid-template-columns:repeat(4,218px);column-gap:22px;row-gap:22px;margin-top:15px}
.card{border:1px solid var(--line);height:378px;text-align:center}
.card .photo{height:190px;border-bottom:1px solid var(--line)}
.card h3{font-size:13px;font-weight:700;color:#222;margin-top:18px}
.card p{font-size:12px;color:var(--muted);line-height:18px;margin:8px 18px 0}
.price{font-size:16px;margin-top:10px}
.price s{color:#888}
.price b{color:var(--price);font-weight:500}
.actions{display:flex;justify-content:center;gap:4px;margin-top:12px}
.actions .btn-yellow{padding:10px 20px}
.wish{width:36px;height:34px;background:#e3e3e3;display:flex;align-items:center;justify-content:center}

/* features */
.features{background:var(--grey-band);height:155px;margin-top:39px;padding-top:26px}
.features .wrap{display:grid;grid-template-columns:repeat(4,1fr)}
.feature h3{display:flex;align-items:center;gap:8px;font-size:16px;font-weight:500;text-transform:uppercase;color:#222}
.feature p{font-size:12px;color:var(--muted);line-height:17px;margin-top:10px;width:200px}
.feature a{color:var(--link);font-size:12px}

/* about */
.about{height:264px;padding-top:32px}
.about .wrap{display:flex;justify-content:space-between}
.about h2{font-size:19px;font-weight:500;text-transform:uppercase;color:#222}
.about-text{width:446px}
.about-text p{font-size:13px;color:#666;line-height:19px;margin-top:10px}
.about-text p:first-of-type{margin-top:22px}
.certs{width:446px}
.cert-grid{display:grid;grid-template-columns:repeat(3,1fr);gap:24px 18px;margin-top:22px}
.cert{height:46px;border-radius:4px}

/* signup */
.signup{background:var(--grey-band);height:87px}
.signup .wrap{display:flex;align-items:center;height:87px}
.signup label{font-size:15px;font-weight:500;text-transform:uppercase;color:#222}
.signup .field{margin-left:20px;width:255px;height:34px;background:#fff;font-size:11px;font-style:italic;color:#999;padding:11px 16px}
.signup .btn-yellow{height:34px;padding:11px 26px}
.signup .divider{width:1px;height:38px;background:#c9c9c9;margin:0 40px 0 40px}
.social{display:flex;gap:8px;margin-left:22px}
.social span{width:34px;height:34px}

/* footer */
.site-footer{background:var(--footer);height:256px;padding-top:29px}
.site-footer .wrap{display:flex}
.col h4{color:var(--yellow);font-size:13px;font-weight:700;text-transform:uppercase;margin-bottom:16px}
.col li{list-style:none;color:var(--footer-text);font-size:12px;line-height:24.5px}
.col.c1{width:160px}.col.c2{width:172px}.col.c3{width:214px}.col.c4{width:187px}
.contact li{display:flex;gap:12px;line-height:18px;margin-bottom:14px}
.bottom-bar{background:var(--footer);border-top:1px solid #2b2b2b;height:55px}
.bottom-bar .wrap{display:flex;justify-content:space-between;align-items:center;height:55px;color:var(--footer-text);font-size:12px}
.pay{display:flex;gap:10px;align-items:center}
.pay b{color:#ddd;font-weight:500;font-size:11px}
</style>
</head>
<body>

<header class="site-header">
  <div class="wrap">
    <nav class="top-links">
      <span>CUSTOMER SERVICE: <span class="phone">+123 456 7890</span></span>
      <a href="#">MY ACCOUNT</a><a href="#">WISH LIST (0)</a><a href="#">CHECKOUT</a><a href="#">LOGIN</a>
    </nav>
    <div class="brand"><span class="brand-dot"></span><span class="brand-name">Calder Vane LED</span></div>
    <div class="search"><span>SEARCH HERE...</span>
      <div class="btn"><svg width="14" height="14" viewBox="0 0 14 14"><circle cx="6" cy="6" r="4.5" fill="none" stroke="#e3262f" stroke-width="1.6"/><line x1="9.3" y1="9.3" x2="13" y2="13" stroke="#e3262f" stroke-width="1.8"/></svg></div>
    </div>
    <div class="cart">
      <svg width="22" height="18" viewBox="0 0 22 18"><path d="M1 1h3l3 11h11l2-8H6" fill="none" stroke="#fcc40a" stroke-width="1.6"/><circle cx="8.5" cy="15.5" r="1.6" fill="#fcc40a"/><circle cx="16.5" cy="15.5" r="1.6" fill="#fcc40a"/></svg>
      <span>0 ITEM(S) - $0.00</span>
    </div>
  </div>
</header>

<nav class="main-nav">
  <div class="wrap">
    <ul>
      <li class="active">Home</li><li>LED Lights Systems</li><li>Truss Systems</li><li>Sound Systems</li><li>Service and Support</li><li>About</li><li>Contact Us</li>
    </ul>
  </div>
</nav>

<section class="hero">
  <div class="wrap">
    <div class="slide" role="img" aria-label="Row of LED light bulbs on a white shelf">
      <h1 class="slide-title">More than<br>100 <em>LED</em> products</h1>
      <a class="btn-yellow" href="#">Click here</a>
      <div class="slide-arrows">
        <span><svg width="8" height="10"><path d="M6 1L2 5l4 4" fill="none" stroke="#fff" stroke-width="2"/></svg></span>
        <span><svg width="8" height="10"><path d="M2 1l4 4-4 4" fill="none" stroke="#fff" stroke-width="2"/></svg></span>
      </div>
    </div>
    <div class="promo sound" role="img" aria-label="Sound systems promotion with a loudspeaker">
      <h3>Sound</h3><h4>Systems</h4><p>Simply dummy printing</p>
      <a class="btn-yellow" href="#">Buy now!</a>
      <span class="off"><b>25</b><small>%</small>OFF</span>
    </div>
    <div class="promo truss" role="img" aria-label="Truss systems promotion with a stage lighting rig">
      <h3>Truss</h3><h4>Systems</h4><p>Simply dummy printing</p>
      <span class="off"><b>25</b><small>%</small>OFF</span>
      <a class="btn-yellow" href="#">Buy now!</a>
    </div>
  </div>
</section>

<section class="featured">
  <div class="wrap">
    <div class="section-head">
      <h2>Featured products</h2>
      <div class="filters"><span class="on">All</span><span>LED Light</span><span>Truss Systems</span><span>Sound Systems</span></div>
    </div>
    <div class="grid">
      <article class="card"><div class="photo" role="img" aria-label="White recessed LED panel light" style="background:radial-gradient(circle,#e6e6e6 30%,#fff 60%)"></div><h3>30W-LED Panel Light</h3><p>simply dummy text the printing and typesetting industry</p><div class="price"><s>$39.00</s> / <b>$33.00</b></div><div class="actions"><a class="btn-yellow">Add to cart</a><span class="wish"><svg width="12" height="11" viewBox="0 0 12 11"><path d="M6 10L1.3 5.4A2.7 2.7 0 016 2a2.7 2.7 0 014.7 3.4z" fill="none" stroke="#888" stroke-width="1.2"/></svg></span></div></article>
      <article class="card"><div class="photo" role="img" aria-label="LED tube light" style="background:linear-gradient(135deg,#fff 20%,#e3e6d2 45%,#f3f3ee 60%,#fff 80%)"></div><h3>20W-T8-LED Tube-UL</h3><p>simply dummy text the printing and typesetting industry</p><div class="price"><s>$39.00</s> / <b>$33.00</b></div><div class="actions"><a class="btn-yellow">Add to cart</a><span class="wish"><svg width="12" height="11" viewBox="0 0 12 11"><path d="M6 10L1.3 5.4A2.7 2.7 0 016 2a2.7 2.7 0 014.7 3.4z" fill="none" stroke="#888" stroke-width="1.2"/></svg></span></div></article>
      <article class="card"><div class="photo" role="img" aria-label="Portable USB speaker system" style="background:radial-gradient(ellipse 35% 45%,#2a2a2a 70%,#fff 72%)"></div><h3>Sistema Sonido Portatil USB</h3><p>simply dummy text the printing and typesetting industry</p><div class="price"><s>$39.00</s> / <b>$33.00</b></div><div class="actions"><a class="btn-yellow">Add to cart</a><span class="wish"><svg width="12" height="11" viewBox="0 0 12 11"><path d="M6 10L1.3 5.4A2.7 2.7 0 016 2a2.7 2.7 0 014.7 3.4z" fill="none" stroke="#888" stroke-width="1.2"/></svg></span></div></article>
      <article class="card"><div class="photo" role="img" aria-label="Stage spotlight on a truss arch" style="background:radial-gradient(circle at 55% 45%,#3a3a3a 25%,#d8d8d8 45%,#fff 65%)"></div><h3>DJ Truss arch</h3><p>simply dummy text the printing and typesetting industry</p><div class="price"><s>$39.00</s> / <b>$33.00</b></div><div class="actions"><a class="btn-yellow">Add to cart</a><span class="wish"><svg width="12" height="11" viewBox="0 0 12 11"><path d="M6 10L1.3 5.4A2.7 2.7 0 016 2a2.7 2.7 0 014.7 3.4z" fill="none" stroke="#888" stroke-width="1.2"/></svg></span></div></article>
      <article class="card"><div class="photo" role="img" aria-label="Four-deck DJ controller" style="background:radial-gradient(ellipse 45% 30%,#2b2b2b 70%,#fff 72%)"></div><h3>Tempo MixStation Quad</h3><p>simply dummy text the printing and typesetting industry</p><div class="price"><s>$39.00</s> / <b>$33.00</b></div><div class="actions"><a class="btn-yellow">Add to cart</a><span class="wish"><svg width="12" height="11" viewBox="0 0 12 11"><path d="M6 10L1.3 5.4A2.7 2.7 0 016 2a2.7 2.7 0 014.7 3.4z" fill="none" stroke="#888" stroke-width="1.2"/></svg></span></div></article>
      <article class="card"><div class="photo" role="img" aria-label="Square LED ceiling panel light" style="background:radial-gradient(circle,#ecebe6 35%,#fff 55%)"></div><h3>30W-LED Panel Light</h3><p>simply dummy text the printing and typesetting industry</p><div class="price"><s>$39.00</s> / <b>$33.00</b></div><div class="actions"><a class="btn-yellow">Add to cart</a><span class="wish"><svg width="12" height="11" viewBox="0 0 12 11"><path d="M6 10L1.3 5.4A2.7 2.7 0 016 2a2.7 2.7 0 014.7 3.4z" fill="none" stroke="#888" stroke-width="1.2"/></svg></span></div></article>
      <article class="card"><div class="photo" role="img" aria-label="DJ table stand with laptop" style="background:linear-gradient(90deg,#fff 30%,#cfd2d5 45%,#bfc3c7 55%,#fff 70%)"></div><h3>DJ Tables &amp; Stands</h3><p>simply dummy text the printing and typesetting industry</p><div class="price"><s>$39.00</s> / <b>$33.00</b></div><div class="actions"><a class="btn-yellow">Add to cart</a><span class="wish"><svg width="12" height="11" viewBox="0 0 12 11"><path d="M6 10L1.3 5.4A2.7 2.7 0 016 2a2.7 2.7 0 014.7 3.4z" fill="none" stroke="#888" stroke-width="1.2"/></svg></span></div></article>
      <article class="card"><div class="photo" role="img" aria-label="Pair of slim T5 LED tubes" style="background:linear-gradient(150deg,#fff 20%,#e4e7f1 40%,#fff 55%,#e4e7f1 70%,#fff 85%)"></div><h3>LumaSlim T5 LED</h3><p>simply dummy text the printing and typesetting industry</p><div class="price"><s>$39.00</s> / <b>$33.00</b></div><div class="actions"><a class="btn-yellow">Add to cart</a><span class="wish"><svg width="12" height="11" viewBox="0 0 12 11"><path d="M6 10L1.3 5.4A2.7 2.7 0 016 2a2.7 2.7 0 014.7 3.4z" fill="none" stroke="#888" stroke-width="1.2"/></svg></span></div></article>
    </div>
  </div>
</section>

<section class="features">
  <div class="wrap">
    <div class="feature"><h3><svg width="20" height="20" viewBox="0 0 20 20"><circle cx="10" cy="10" r="6.5" fill="none" stroke="#222" stroke-width="4" stroke-dasharray="3 2.1"/><circle cx="10" cy="10" r="5" fill="#222"/><circle cx="10" cy="10" r="2.2" fill="#e6e6e6"/></svg>Technology</h3><p>t is long established fact the reader will be distracted by the readable content of a page...</p><a href="#">Read More »</a></div>
    <div class="feature"><h3><svg width="20" height="20" viewBox="0 0 20 20"><circle cx="5" cy="5" r="3" fill="none" stroke="#222" stroke-width="2.2"/><circle cx="15" cy="15" r="3" fill="none" stroke="#222" stroke-width="2.2"/><line x1="16" y1="2" x2="4" y2="18" stroke="#222" stroke-width="2.4"/></svg>Price</h3><p>t is long established fact the reader will be distracted by the readable content of a page...</p><a href="#">Read More »</a></div>
    <div class="feature"><h3><svg width="20" height="20" viewBox="0 0 20 20"><rect x="2" y="4" width="14" height="14" fill="none" stroke="#222" stroke-width="2"/><path d="M5 10l4 4 9-11" fill="none" stroke="#222" stroke-width="2.6"/></svg>Quality</h3><p>t is long established fact the reader will be distracted by the readable content of a page...</p><a href="#">Read More »</a></div>
    <div class="feature"><h3><svg width="20" height="20" viewBox="0 0 20 20"><circle cx="10" cy="10" r="8" fill="none" stroke="#222" stroke-width="2"/><circle cx="10" cy="10" r="3.5" fill="#222"/></svg>Warranty</h3><p>t is long established fact the reader will be distracted by the readable content of a page...</p><a href="#">Returns Policy »</a></div>
  </div>
</section>

<section class="about">
  <div class="wrap">
    <div class="about-text">
      <h2>About Calder Vane LED</h2>
      <p>It is a long established fact that a reader will be distracted by the readable content of a page when looking at its layout. The point of using Lorem Ipsum is that it has a more-or-less normal distribution of Content here, content here, making it look like readable English.</p>
      <p>Many desktop publishing packages and web page editors now use Lorem Ipsum as their default model text, and a search for 'lorem ipsum' will uncover many web sites still in their infancy...</p>
    </div>
    <div class="certs">
      <h2>Product certification</h2>
      <div class="cert-grid">
        <span class="cert" role="img" aria-label="Certification badge" style="background:#d9e7f0"></span>
        <span class="cert" role="img" aria-label="Certification badge" style="background:#e2e2e2"></span>
        <span class="cert" role="img" aria-label="Certification badge" style="background:#ecdcdc"></span>
        <span class="cert" role="img" aria-label="Certification badge" style="background:#f3d9d9"></span>
        <span class="cert" role="img" aria-label="Certification badge" style="background:#d8eaf2"></span>
        <span class="cert" role="img" aria-label="Certification badge" style="background:#dfeed6"></span>
      </div>
    </div>
  </div>
</section>

<section class="signup">
  <div class="wrap">
    <label>Sign up for deals:</label>
    <div class="field">Enter Your Email</div>
    <a class="btn-yellow" href="#">Sign up</a>
    <span class="divider"></span>
    <label>Stay connected:</label>
    <div class="social">
      <span role="img" aria-label="Social network link" style="background:#3b5a9a"></span>
      <span role="img" aria-label="Social network link" style="background:#2ba7e0"></span>
      <span role="img" aria-label="Social network link" style="background:#0e76a8"></span>
      <span role="img" aria-label="Social network link" style="background:#e2453a"></span>
    </div>
  </div>
</section>

<footer class="site-footer">
  <div class="wrap">
    <div class="col c1"><h4>Quick links</h4><ul><li>Home</li><li>Products</li><li>Services</li><li>About Us</li><li>FAQ's</li></ul></div>
    <div class="col c2"><h4>Need help?</h4><ul><li>See All Help</li><li>Returns</li><li>Shipping</li><li>Warranty</li><li>Contact Us</li></ul></div>
    <div class="col c3"><h4>Policies &amp; info</h4><ul><li>Terms and Conditions</li><li>Policy for Sellers</li><li>Policy for Buyers</li><li>Shipping &amp; Refund Policies</li><li>Wholesale Policy</li><li>Privacy Policy</li></ul></div>
    <div class="col c4"><h4>My account</h4><ul><li>Sign in</li><li>Track Order</li></ul></div>
    <div class="col contact"><h4>Contact us</h4><ul>
      <li><svg width="12" height="16" viewBox="0 0 12 16"><path d="M6 15S1 9 1 6a5 5 0 0110 0c0 3-5 9-5 9z" fill="#8a8a8a"/><circle cx="6" cy="6" r="2" fill="#161616"/></svg><span>Lorem Ipsum is simply dummy<br>Marlow Ridge, AB T0X 4K2</span></li>
      <li><svg width="12" height="14" viewBox="0 0 12 14"><path d="M2 1l3 1 1 3-2 1.5a8 8 0 003.5 3.5L9 8l3 1v3l-2 1C5 12 1 8 0 3z" fill="#8a8a8a"/></svg><span>Phone:<br>(123) 456 7890</span></li>
      <li><svg width="12" height="10" viewBox="0 0 12 10"><rect width="12" height="9" fill="#8a8a8a"/><path d="M0 0l6 5 6-5" fill="none" stroke="#161616" stroke-width="1.2"/></svg><span>Email:<br>info@caldervaneled.com</span></li>
    </ul></div>
  </div>
</footer>
<div class="bottom-bar">
  <div class="wrap">
    <span>Copyright © 2016 - Calder Vane LED, All Rights Reserved</span>
    <div class="pay">Accepted Payment : <b>Cardo</b><b>PayLink</b><b>Vexa</b><b>Mintcard</b></div>
  </div>
</div>

</body>
</html>
```